SaaS Early tech startup business card design

Unique design for experience ecommerce platform company. the business cards will be used by executive members. conformance with color code is required.

```html
<!DOCTYPE html>
<html lang="en">
<head>
<meta charset="utf-8">
<title>nuvio business card</title>
<link href="https://fonts.googleapis.com/css2?family=Roboto:wght@400;700&family=Montserrat:wght@400&display=swap" rel="stylesheet">
<style>
  :root {
    --stage: #6b6868;
    --card: #1f2136;
    --card-deep: #1c1e33;
    --teal: #1aa99a;
    --blue-wave: #1b4a63;
    --text-light: #ffffff;
  }
  html, body {
    margin: 0;
    padding: 0;
    width: 1200px;
    height: 1200px;
    overflow: hidden;
    background: var(--stage);
  }
  .canvas {
    position: relative;
    width: 1200px;
    height: 1200px;
    font-family: "Roboto", Arial, sans-serif;
  }
  .card {
    position: absolute;
    width: 595px;
    height: 350px;
    border-radius: 26px;
    background: var(--card);
    overflow: hidden;
  }
  .card-front { left: 298px; top: 198px; }
  .card-back { left: 292px; top: 636px; }

  .front-texture {
    position: absolute;
    inset: 0;
    background:
      radial-gradient(ellipse 60% 45% at 50% 40%, rgba(27, 74, 99, 0.45), transparent 70%),
      radial-gradient(ellipse 25% 60% at 20% 80%, rgba(27, 74, 99, 0.3), transparent 70%),
      radial-gradient(ellipse 25% 60% at 85% 75%, rgba(27, 74, 99, 0.3), transparent 70%),
      var(--card-deep);
  }
  .wordmark {
    position: absolute;
    left: 0;
    right: 0;
    text-align: center;
    color: var(--teal);
    font-weight: 700;
    line-height: 1;
    letter-spacing: -0.02em;
  }
  .card-front .wordmark { top: 85px; font-size: 150px; }
  .tagline {
    position: absolute;
    left: 0;
    right: 0;
    top: 245px;
    text-align: center;
    font-family: "Montserrat", Arial, sans-serif;
    font-size: 18px;
    letter-spacing: 0.42em;
    padding-left: 0.42em;
    color: var(--text-light);
  }

  .card-back .wordmark { top: 43px; font-size: 96px; }
  .holder-name {
    position: absolute;
    left: 0; right: 0;
    top: 188px;
    text-align: center;
    color: var(--teal);
    font-weight: 700;
    font-size: 22px;
    letter-spacing: -0.02em;
  }
  .holder-role {
    position: absolute;
    left: 0; right: 0;
    top: 216px;
    text-align: center;
    color: var(--text-light);
    font-size: 16px;
  }
  .contact-line {
    position: absolute;
    left: 0; right: 0;
    display: flex;
    justify-content: center;
    align-items: center;
    gap: 16px;
    color: var(--text-light);
    font-size: 16px;
  }
  .contact-line.primary { top: 263px; }
  .contact-line.address { top: 285px; }
  .contact-item {
    display: flex;
    align-items: center;
    gap: 14px;
  }
  .contact-item svg { width: 15px; height: 15px; fill: var(--teal); }
  .accent-band {
    position: absolute;
    left: 0; right: 0; bottom: 0;
    height: 9px;
    background: var(--teal);
  }
</style>
</head>
<body>
<main class="canvas">
  <section class="card card-front">
    <div class="front-texture" role="img" aria-label="Faint wavy line pattern in deep blue behind the brand name"></div>
    <div class="wordmark">nuvio</div>
    <div class="tagline">SHAPED FOR YOU</div>
  </section>

  <section class="card card-back">
    <div class="wordmark">nuvio</div>
    <div class="holder-name">Darian K.</div>
    <div class="holder-role">CTO/Owner</div>

    <div class="contact-line primary">
      <span class="contact-item">
        <svg viewBox="0 0 16 16" aria-hidden="true"><path d="M2 6c0-2 2-3 6-3s6 1 6 3v1h-3V6H5v1H2zM4 8h8l2 5H2z"/></svg>
        (00) 0111 NUVO
      </span>
      <span class="contact-item">
        <svg viewBox="0 0 16 16" aria-hidden="true"><path d="M1 3h14v10H1zM2.5 4.5 8 9l5.5-4.5z" fill-rule="evenodd"/></svg>
        info@nuvio.net
      </span>
      <span class="contact-item">
        <svg viewBox="0 0 16 16" aria-hidden="true"><path d="M8 1a7 7 0 1 0 0 14A7 7 0 0 0 8 1zm0 1.5c1 1.2 1.6 3 1.7 4.8H6.3C6.4 5.5 7 3.7 8 2.5zM2.6 8.7h2.3c.1 1.8.6 3.4 1.4 4.5a5.5 5.5 0 0 1-3.7-4.5zm0-1.4a5.5 5.5 0 0 1 3.7-4.5c-.8 1.1-1.3 2.7-1.4 4.5zm3.7 1.4h3.4c-.1 1.8-.7 3.6-1.7 4.8-1-1.2-1.6-3-1.7-4.8zm3.4 4.5c.8-1.1 1.3-2.7 1.4-4.5h2.3a5.5 5.5 0 0 1-3.7 4.5zm1.4-5.9c-.1-1.8-.6-3.4-1.4-4.5a5.5 5.5 0 0 1 3.7 4.5z"/></svg>
        www.nuvio.net
      </span>
    </div>
    <div class="contact-line address">
      <span class="contact-item">
        <svg viewBox="0 0 16 16" aria-hidden="true"><path d="M8 1a5 5 0 0 0-5 5c0 3.5 5 9 5 9s5-5.5 5-9a5 5 0 0 0-5-5zm0 7a2 2 0 1 1 0-4 2 2 0 0 1 0 4z"/></svg>
        Harbor Point Tower, Dubai, Media District, UAE
      </span>
    </div>
    <div class="accent-band"></div>
  </section>
</main>
</body>
</html>
```